Advanced Therapeutic Massage Therapist

I need a business card advertising my massage services as an advanced therapeutic massage therapist. I offer advanced therapeutic massage, swedish and deep tissue. I want to create a simple, professional and feminine card. I like bright colours and creativity.

I prefer a bold and experimental approach rather than something status-quo. A card to suggest therapeutic healing through dynamic massage. Motifs, shapes or layout which suggest movement and flow.
Updates

Target Market(s)

Everybody!

Industry/Entity Type

Health And Wellness

Contact Information for Business Card

The card should include:
My name, logo, services offered and my contact details.

Sláine Dunleavy
Massage Therapist

- Swedish - Deep Tissue - Advanced Therapeutic

Phone: (+353) 87 216 4093
Email: regenerate@slainedunleavy-example.com
Website: www.slainedunlevy-example.com

Font styles to use
Serif
Sans Serif
Decorative
Script

Colors

Designer to choose colors to be used in the design.

Requirements
Must have
• An example may contain something like this, yet concise:
• "Sláine Dunleavy
• Massage Therapist
• - Swedish - Deep Tissue - Advanced Therapeutic"
Nice to have
• This sentence is optional:
• Imagery such as a logo or symbol. I have attached a file containing a logo I had produced however the name is incorrect now as it is "Sláine" not "Nelly". It could be edited to change it to Sláine.
• I have sent the file as .psd .jpg. .pdf and .png
• I like when the card conveys energy, movement, pressure points, flow etc.
• I just like the designer to follow their own style and ideas. I like bright colours but must have a lot of a base colour to offset it. I really prefer them to follow their own inspiration. That is my preference.
Should not have
• Pine trees, non-native trees to Britain and Ireland, exotic flowers or animals that are not native to Britain and Ireland.
• I don't like brown as the background colour of the card.
• The cars shouldn't look like a wedding invitation i.e too many floral type designs.

```html
<!DOCTYPE html>
<html lang="en">
<head>
<meta charset="utf-8">
<title>Sláine Dunleavy – Massage Therapist Business Card</title>
<link rel="stylesheet" href="https://fonts.googleapis.com/css2?family=Great+Vibes&family=Josefin+Sans:wght@300&family=Questrial&family=Fira+Sans+Condensed:wght@500&display=swap">
<style>
  :root {
    --backdrop: #6a6a6a;
    --card: #1f1f1f;
    --card-edge: #8a8a8a;
    --ink: #f4f2ee;
    --accent: #72c2a4;
    --mark-light: #bfe4d8;
    --mark-mid: #8fcab6;
  }
  html, body {
    margin: 0;
    padding: 0;
    overflow: hidden;
  }
  body {
    width: 1200px;
    height: 550px;
    background: var(--backdrop);
    position: relative;
  }
  .card {
    position: absolute;
    top: 157px;
    width: 390px;
    height: 235px;
    background: var(--card);
    box-shadow: 0 0 0 1px var(--card-edge);
    color: var(--ink);
    text-align: center;
  }
  .card--front { left: 195px; }
  .card--back { left: 614px; }

  .brand-mark {
    position: absolute;
    left: 137px;
    top: 31px;
    width: 116px;
    height: 116px;
    border-radius: 50%;
    background: radial-gradient(circle at 50% 45%, var(--mark-light), var(--mark-mid));
  }
  .name {
    position: absolute;
    left: 0;
    right: 0;
    font-family: "Great Vibes", cursive;
    font-size: 27px;
    line-height: 1;
    margin: 0;
    font-weight: 400;
  }
  .role {
    position: absolute;
    left: 0;
    right: 0;
    font-family: "Josefin Sans", sans-serif;
    font-weight: 300;
    font-size: 10px;
    letter-spacing: 1.6px;
    line-height: 1;
    margin: 0;
  }
  .card--front .name { top: 149px; }
  .card--front .role { top: 177px; }
  .card--back .name { top: 66px; }
  .card--back .role { top: 94px; }

  .qualification {
    position: absolute;
    left: 0;
    right: 0;
    top: 210px;
    margin: 0;
    font-family: "Fira Sans Condensed", sans-serif;
    font-weight: 500;
    font-size: 10px;
    color: var(--accent);
  }
  .contact {
    position: absolute;
    left: 0;
    right: 0;
    top: 118px;
    margin: 0;
    padding: 0;
    list-style: none;
    font-family: "Questrial", sans-serif;
    font-size: 11px;
    line-height: 16.5px;
  }
  .services {
    position: absolute;
    left: 0;
    right: 0;
    top: 211px;
    margin: 0;
    font-family: "Questrial", sans-serif;
    font-size: 11px;
    color: var(--accent);
  }
</style>
</head>
<body>
  <section class="card card--front">
    <div class="brand-mark" role="img" aria-label="Brand emblem area"></div>
    <h1 class="name">Sláine Dunleavy</h1>
    <p class="role">massage therapist</p>
    <p class="qualification">ATMB qualified, specializing in Advanced Therapeutic &amp; Deep Tissue Massage</p>
  </section>

  <section class="card card--back">
    <h2 class="name">Sláine Dunleavy</h2>
    <p class="role">massage therapist</p>
    <ul class="contact">
      <li>(+353) 87 216 4093</li>
      <li>regenerate@slainedunleavy-example.com</li>
      <li>www.slainedunlevy-example.com</li>
    </ul>
    <p class="services">Swedish - Deep Tissue - Advanced Therapeutic</p>
  </section>
</body>
</html>
```